Grafic Ad for a Printmagazine about Tractor Vehicles

We need for a Geman Printmagazine about Tractors a Grafic Design in different sizes. Our Website and corporate Design: https://www.kalvimo.de You can work with the uploaded files . The round Logo with shaking hands should be included in your Designs somehow. Perhaps as a transparent in the background or placed in a corner. The Font used for the URL is Days (typelodge.com/days.font) Please use this Font or a other similar for the URL "kalvimo.de" and expand it to "www.kalvimo.de/traktorwert" For the other Text parts (first line) and (second line) you can use a other font which you prefer. We need the grafics as .jpg in the pixel sizes: 472x496, 437x614, 307x437 (Print would be DPI 300). Goal is a eye-catching design for the later print ad. Have fun and be creative ;)

Logo Text

"Traktor Bewertung" (first line), " Kurzgutachen für Verkauf, Kauf oder Versicherung" (second line), "www.kalvimo.de/traktorwert" (third line)

Logo styles of interest
Pictorial/Combination Logo
Font styles to use
Other font styles liked:
• Days.tff for the URL

Colors
0054AA
0677BA
7BADD7
CADEEF
E8F1F8
0094D4
00A9DD
6FCCEA
C7EBF8
E9F6FB

```html
<!DOCTYPE html>
<html lang="de">
<head>
<meta charset="utf-8">
<title>Traktor Bewertung – Anzeigen</title>
<link href="https://fonts.googleapis.com/css2?family=Days+One&display=swap" rel="stylesheet">
<style>
  :root{
    --sheet:#e6e6e6;
    --white:#ffffff;
    --brand-blue:#1e7fc4;
    --deep-blue:#0677ba;
    --sky:#8fd3f2;
    --swoosh:#4a9fd9;
    --swoosh-light:#8ec6ea;
    --ink-grey:#555a60;
    --photo-a:#6f9fcf;
    --photo-b:#2f5f8f;
  }
  *{margin:0;padding:0;box-sizing:border-box}
  html,body{width:1200px;height:2371px;overflow:hidden;background:var(--sheet)}
  .sheet{position:relative;width:1200px;height:2371px}
  .ad{position:absolute;display:block;overflow:hidden;background:var(--white)}
  .ad--large{left:96px;top:94px;width:991px;height:704px}
  .ad--medium{left:192px;top:882px;width:800px;height:761px}
  .ad--small{left:239px;top:1734px;width:706px;height:496px}
  .ad text{font-family:'Days One',sans-serif}
  .brand-name{fill:var(--brand-blue)}
  .brand-dot{fill:var(--brand-blue)}
  .title-grey{fill:var(--ink-grey)}
  .title-blue{fill:var(--brand-blue)}
  .wave-main{fill:url(#bandGradient)}
  .wave-swoosh{fill:var(--swoosh)}
  .wave-swoosh-light{fill:var(--swoosh-light)}
  .tractor-photo{fill:url(#photoGradient)}
  .url-pill{fill:url(#pillGradient);stroke:#cfe8f8;stroke-width:2}
  .url-text{fill:var(--white)}
  .service-text{fill:var(--white)}
  .icon{fill:none;stroke:var(--white);stroke-width:2.2;stroke-linejoin:round;stroke-linecap:round}
  .star{fill:url(#starGradient);stroke:#a9d2f0;stroke-width:0.04}
</style>
</head>
<body>
<div class="sheet">

<svg width="0" height="0" style="position:absolute" aria-hidden="true">
  <defs>
    <linearGradient id="bandGradient" x1="0" y1="0" x2="0" y2="1">
      <stop offset="0" stop-color="#1b7cc3"/>
      <stop offset="0.55" stop-color="#4a9fd9"/>
      <stop offset="1" stop-color="#93d6f3"/>
    </linearGradient>
    <linearGradient id="photoGradient" x1="0" y1="0" x2="1" y2="1">
      <stop offset="0" stop-color="#7fb0dc"/>
      <stop offset="1" stop-color="#2e5c8a"/>
    </linearGradient>
    <linearGradient id="pillGradient" x1="0" y1="0" x2="0" y2="1">
      <stop offset="0" stop-color="#5aaee4"/>
      <stop offset="1" stop-color="#1970b8"/>
    </linearGradient>
    <linearGradient id="starGradient" x1="0" y1="0" x2="0" y2="1">
      <stop offset="0" stop-color="#5aaee6"/>
      <stop offset="1" stop-color="#2a85cc"/>
    </linearGradient>
    <filter id="softShadow" x="-20%" y="-40%" width="140%" height="180%">
      <feDropShadow dx="2" dy="3" stdDeviation="2.5" flood-color="#0b3a66" flood-opacity="0.55"/>
    </filter>
    <symbol id="star" viewBox="-1 -1 2 2">
      <polygon class="star" points="0,-1 0.235,-0.324 0.951,-0.309 0.38,0.124 0.588,0.809 0,0.4 -0.588,0.809 -0.38,0.124 -0.951,-0.309 -0.235,-0.324"/>
    </symbol>
    <symbol id="icon-tag" viewBox="0 0 48 48">
      <path class="icon" d="M6 14 L22 6 L42 26 L26 42 L6 28 Z"/>
      <circle class="icon" cx="14" cy="15" r="2.5"/>
      <path class="icon" d="M24 20 L32 28 M23 27 L31 35"/>
    </symbol>
    <symbol id="icon-money" viewBox="0 0 60 40">
      <rect class="icon" x="3" y="12" width="36" height="20" rx="2"/>
      <path class="icon" d="M21 16 V28 M25 18.5 C23 16.5 17 17 18 20.5 C19 23 25 21.5 24.5 25 C24 28 18 27.5 16.5 25.5"/>
      <path class="icon" d="M39 18 L48 10 L56 12 L56 22 L46 24 L39 26"/>
    </symbol>
    <symbol id="icon-shield" viewBox="0 0 40 48">
      <path class="icon" d="M20 3 L36 9 V22 C36 34 28 41 20 45 C12 41 4 34 4 22 V9 Z"/>
      <path class="icon" d="M12 24 L18 30 L29 17"/>
    </symbol>
  </defs>
</svg>

<!-- Large format -->
<svg class="ad ad--large" viewBox="0 0 991 704">
  <rect width="991" height="704" fill="#fff"/>
  <path class="wave-swoosh" d="M0,170 C60,232 200,252 336,250 C200,266 60,252 0,210 Z"/>
  <path class="wave-swoosh-light" d="M600,200 C770,168 900,170 991,198 L991,250 C900,218 770,198 600,200 Z"/>
  <path class="wave-main" d="M0,262 C300,196 640,168 991,240 L991,704 L0,704 Z"/>

  <circle class="brand-dot" cx="150" cy="100" r="42"/>
  <text class="brand-name" x="150" y="180" font-size="26" text-anchor="middle">kalvimo.de</text>

  <use href="#star" x="502" y="54" width="76" height="76"/>
  <use href="#star" x="558" y="44" width="96" height="96"/>
  <use href="#star" x="624" y="28" width="120" height="120"/>
  <use href="#star" x="714" y="44" width="96" height="96"/>
  <use href="#star" x="790" y="54" width="76" height="76"/>

  <text x="689" y="182" font-size="44" text-anchor="middle"><tspan class="title-grey">Traktor </tspan><tspan class="title-blue">Bewertung</tspan></text>

  <rect class="tractor-photo" x="156" y="290" width="378" height="288" rx="24" role="img" aria-label="Foto eines blau lackierten Oldtimer-Traktors"/>

  <rect class="url-pill" x="52" y="588" width="606" height="60" rx="30" filter="url(#softShadow)"/>
  <text class="url-text" x="355" y="630" font-size="31" text-anchor="middle">www.kalvimo.de/traktorwert</text>

  <g filter="url(#softShadow)">
    <text class="service-text" x="818" y="275" font-size="21" text-anchor="middle">Kurzgutachen für</text>
    <use href="#icon-tag" x="792" y="320" width="54" height="54"/>
    <text class="service-text" x="818" y="412" font-size="30" text-anchor="middle">Verkauf,</text>
    <use href="#icon-money" x="784" y="440" width="68" height="46"/>
    <text class="service-text" x="818" y="526" font-size="30" text-anchor="middle">Kauf oder</text>
    <use href="#icon-shield" x="796" y="548" width="44" height="54"/>
    <text class="service-text" x="818" y="640" font-size="30" text-anchor="middle">Versicherung</text>
  </g>
</svg>

<!-- Medium format -->
<svg class="ad ad--medium" viewBox="0 0 800 761">
  <rect width="800" height="761" fill="#fff"/>
  <path class="wave-swoosh" d="M0,196 C60,254 180,272 280,268 C180,288 60,276 0,238 Z"/>
  <path class="wave-swoosh-light" d="M520,230 C650,212 740,214 800,226 L800,262 C740,244 650,232 520,230 Z"/>
  <path class="wave-main" d="M0,290 C260,240 560,216 800,280 L800,761 L0,761 Z"/>

  <circle class="brand-dot" cx="126" cy="96" r="46"/>
  <text class="brand-name" x="130" y="181" font-size="28" text-anchor="middle">kalvimo.de</text>

  <use href="#star" x="336" y="66" width="72" height="72"/>
  <use href="#star" x="394" y="56" width="92" height="92"/>
  <use href="#star" x="460" y="42" width="116" height="116"/>
  <use href="#star" x="550" y="56" width="92" height="92"/>
  <use href="#star" x="626" y="66" width="72" height="72"/>

  <text x="522" y="193" font-size="44" text-anchor="middle"><tspan class="title-grey">Traktor </tspan><tspan class="title-blue">Bewertung</tspan></text>

  <rect class="tractor-photo" x="84" y="330" width="360" height="282" rx="24" role="img" aria-label="Foto eines blau lackierten Oldtimer-Traktors"/>

  <rect class="url-pill" x="40" y="658" width="458" height="46" rx="23" filter="url(#softShadow)"/>
  <text class="url-text" x="269" y="689" font-size="24" text-anchor="middle">www.kalvimo.de/traktorwert</text>

  <g filter="url(#softShadow)">
    <text class="service-text" x="644" y="315" font-size="22" text-anchor="middle">Kurzgutachen für</text>
    <use href="#icon-tag" x="615" y="358" width="58" height="58"/>
    <text class="service-text" x="644" y="456" font-size="32" text-anchor="middle">Verkauf,</text>
    <use href="#icon-money" x="608" y="486" width="72" height="48"/>
    <text class="service-text" x="644" y="576" font-size="32" text-anchor="middle">Kauf oder</text>
    <use href="#icon-shield" x="620" y="598" width="48" height="58"/>
    <text class="service-text" x="644" y="696" font-size="32" text-anchor="middle">Versicherung</text>
  </g>
</svg>

<!-- Small format -->
<svg class="ad ad--small" viewBox="0 0 706 496">
  <rect width="706" height="496" fill="#fff"/>
  <path class="wave-swoosh" d="M0,102 C50,146 150,160 240,160 C150,174 50,166 0,136 Z"/>
  <path class="wave-swoosh-light" d="M480,132 C590,116 660,118 706,128 L706,160 C660,146 590,134 480,132 Z"/>
  <path class="wave-main" d="M0,170 C230,136 480,118 706,168 L706,496 L0,496 Z"/>

  <circle class="brand-dot" cx="101" cy="58" r="34"/>
  <text class="brand-name" x="103" y="117" font-size="19" text-anchor="middle">kalvimo.de</text>

  <use href="#star" x="371" y="36" width="48" height="48"/>
  <use href="#star" x="409" y="30" width="60" height="60"/>
  <use href="#star" x="452" y="20" width="76" height="76"/>
  <use href="#star" x="511" y="30" width="60" height="60"/>
  <use href="#star" x="559" y="36" width="48" height="48"/>

  <text x="492" y="120" font-size="28" text-anchor="middle"><tspan class="title-grey">Traktor </tspan><tspan class="title-blue">Bewertung</tspan></text>

  <rect class="tractor-photo" x="79" y="210" width="240" height="186" rx="18" role="img" aria-label="Foto eines blau lackierten Oldtimer-Traktors"/>

  <rect class="url-pill" x="31" y="422" width="363" height="38" rx="19" filter="url(#softShadow)"/>
  <text class="url-text" x="212" y="448" font-size="19" text-anchor="middle">www.kalvimo.de/traktorwert</text>

  <g filter="url(#softShadow)">
    <text class="service-text" x="413" y="194" font-size="22">Kurzgutachen für</text>
    <use href="#icon-tag" x="414" y="242" width="44" height="44"/>
    <text class="service-text" x="478" y="271" font-size="22">Verkauf,</text>
    <use href="#icon-money" x="408" y="338" width="56" height="36"/>
    <text class="service-text" x="478" y="363" font-size="22">Kauf oder</text>
    <use href="#icon-shield" x="418" y="424" width="36" height="44"/>
    <text class="service-text" x="478" y="454" font-size="22">Versicherung</text>
  </g>
</svg>

</div>
</body>
</html>
```